Q&J RESTORATION

I want a brochure similiar to the example i've attached.
My company name is Q&J Restoration. The website is: Q-J-Restoration.example.
The phone number is 919.555.0147.

I don't like the "yellow" being the main color of the example so I'm open to suggestions. I want something CLEAN & Simple, like our logo . This will be a bi fold brochure

```html
<!DOCTYPE html>
<html lang="en">
<head>
<meta charset="utf-8">
<title>Q&amp;J Restoration – Bi-fold Brochure</title>
<link rel="stylesheet" href="https://fonts.googleapis.com/css2?family=Poppins:wght@400;500;600;700;800&display=swap">
<style>
  :root{
    --stage:#b9b9b9;
    --paper:#efeceb;
    --ink:#1d1d1f;
    --night:#121213;
    --night-soft:#2b2b2d;
    --brand-blue:#1f77b7;
    --sky-blue:#5db9e9;
    --accent-blue:#2c9fe2;
    --white:#ffffff;
    --muted:#d9d9d9;
  }
  html,body{margin:0;padding:0;}
  body{
    width:1200px;height:2547px;overflow:hidden;
    background:var(--stage);
    position:relative;
    font-family:"Poppins",sans-serif;
  }
  .sheet{position:absolute;display:block;box-shadow:0 14px 30px rgba(0,0,0,.28);}
  .sheet--front{left:370px;top:100px;width:460px;height:650px;}
  .sheet--outer{left:80px;top:905px;width:1040px;height:735px;}
  .sheet--inner{left:105px;top:1760px;width:990px;height:700px;}

  .paper{fill:var(--paper);}
  .night{fill:url(#nightPhoto);}
  .band-blue{fill:url(#blueBand);}
  .band-sky{fill:var(--sky-blue);}
  .brand-name{font-family:"Poppins",sans-serif;font-weight:500;fill:var(--ink);}
  .brand-name--light{fill:var(--white);}
  .tagline-small{font-family:"Poppins",sans-serif;font-weight:700;fill:var(--white);font-size:21px;letter-spacing:1px;}
  .tagline-big{font-family:"Poppins",sans-serif;font-weight:800;fill:var(--white);font-size:46px;letter-spacing:1px;}
  .web{font-family:"Poppins",sans-serif;font-weight:500;fill:var(--ink);font-size:17px;letter-spacing:2px;}
  .band-text{font-family:"Poppins",sans-serif;font-weight:700;fill:var(--night);font-size:17px;}
  .contact{font-family:"Poppins",sans-serif;font-weight:500;fill:var(--white);font-size:15px;}
  .contact--phone{font-weight:700;font-size:17px;letter-spacing:1px;}
  .icon-disc{fill:var(--white);}
  .icon-line{fill:none;stroke:var(--night);stroke-width:1.6;stroke-linecap:round;stroke-linejoin:round;}
  .photo{fill:url(#couplePhoto);}
  .chevron-edge{fill:none;stroke:var(--white);stroke-width:7;stroke-linejoin:miter;}
  .panel{fill:var(--night);}
  .headline{font-family:"Poppins",sans-serif;font-weight:700;font-size:31px;fill:var(--white);}
  .headline--blue{fill:var(--accent-blue);}
  .subhead{font-family:"Poppins",sans-serif;font-weight:600;font-size:16px;fill:var(--white);}
  .pillar-band{fill:var(--paper);}
  .pillar{font-family:"Poppins",sans-serif;font-weight:600;font-size:18px;fill:var(--night);}
  .tick-disc{fill:var(--accent-blue);}
  .tick{fill:none;stroke:var(--white);stroke-width:1.8;stroke-linecap:round;stroke-linejoin:round;}
  .feature-ring{fill:var(--white);stroke:var(--night-soft);stroke-width:3;}
  .feature-icon{fill:none;stroke:var(--brand-blue);stroke-width:2;stroke-linecap:round;stroke-linejoin:round;}
  .feature-icon-fill{fill:var(--brand-blue);}
  .feature-title{font-family:"Poppins",sans-serif;font-weight:600;font-size:16px;fill:var(--accent-blue);}
  .feature-body{font-family:"Poppins",sans-serif;font-weight:400;font-size:9.6px;fill:var(--muted);}
  .promise{font-family:"Poppins",sans-serif;font-weight:500;font-size:15px;fill:var(--white);letter-spacing:.5px;}
</style>
</head>
<body>

<svg width="0" height="0" style="position:absolute" aria-hidden="true">
  <defs>
    <linearGradient id="nightPhoto" x1="0" y1="0" x2="1" y2="1">
      <stop offset="0" stop-color="#2a2a2c"/>
      <stop offset=".5" stop-color="#141415"/>
      <stop offset="1" stop-color="#1f1f21"/>
    </linearGradient>
    <linearGradient id="blueBand" x1="0" y1="0" x2="1" y2="1">
      <stop offset="0" stop-color="#1a6aa8"/>
      <stop offset="1" stop-color="#2384c6"/>
    </linearGradient>
    <linearGradient id="couplePhoto" x1="0" y1="0" x2="1" y2="1">
      <stop offset="0" stop-color="#5e5b58"/>
      <stop offset=".45" stop-color="#77716b"/>
      <stop offset=".75" stop-color="#4d4945"/>
      <stop offset="1" stop-color="#8a8580"/>
    </linearGradient>
  </defs>
</svg>

<!-- Front cover -->
<svg class="sheet sheet--front" viewBox="0 0 500 707" xmlns="http://www.w3.org/2000/svg">
  <rect class="night" x="0" y="0" width="500" height="707" role="img" aria-label="Dark photo of water damage"/>
  <polygon class="paper" points="190,0 500,0 500,707 18,707 18,320"/>
  <rect class="band-blue" x="18" y="320" width="482" height="175"/>
  <text class="brand-name" x="320" y="190" font-size="30" text-anchor="middle">Q&amp;J Restoration</text>
  <text class="tagline-small" x="50" y="362">THREE GENERATIONS OF</text>
  <text class="tagline-big" x="44" y="412">RESTORATION</text>
  <text class="tagline-big" x="44" y="462">EXPERIENCE</text>
  <text class="web" x="50" y="620">www.q-j-restoration.example</text>
</svg>

<!-- Outer spread: back + front -->
<svg class="sheet sheet--outer" viewBox="0 0 1000 707" xmlns="http://www.w3.org/2000/svg">
  <rect class="night" x="0" y="0" width="1000" height="707" role="img" aria-label="Dark photo of a flooded room"/>
  <polygon class="band-sky" points="0,292 580,335 580,375 0,332"/>
  <polygon class="paper" points="690,0 1000,0 1000,707 518,707 518,320"/>
  <rect class="band-blue" x="518" y="320" width="482" height="175"/>

  <text class="brand-name brand-name--light" x="250" y="237" font-size="28" text-anchor="middle">Q&amp;J Restoration</text>
  <text class="band-text" transform="translate(30,318) rotate(4.2)">Insurance Claim? We're on Your Team.</text>

  <circle class="icon-disc" cx="250" cy="410" r="11"/>
  <path class="icon-line" d="M245,404 q-2,6 4,12 q6,6 10,3 l-2,-3 l-3,1 q-4,-2 -6,-6 l1,-3 z"/>
  <text class="contact contact--phone" x="250" y="446" text-anchor="middle">919.555.0147</text>

  <circle class="icon-disc" cx="250" cy="480" r="11"/>
  <rect class="icon-line" x="243" y="475" width="14" height="10" rx="1"/>
  <path class="icon-line" d="M243,476 l7,5 l7,-5"/>
  <text class="contact" x="250" y="515" text-anchor="middle">info@q-j-restoration.example</text>

  <circle class="icon-disc" cx="250" cy="549" r="11"/>
  <circle class="icon-line" cx="250" cy="549" r="6.5"/>
  <path class="icon-line" d="M243.5,549 h13 M250,542.5 q-4,6.5 0,13 q4,-6.5 0,-13"/>
  <text class="contact" x="250" y="584" text-anchor="middle">www.q-j-restoration.example</text>

  <text class="brand-name" x="820" y="190" font-size="30" text-anchor="middle">Q&amp;J Restoration</text>
  <text class="tagline-small" x="550" y="362">THREE GENERATIONS OF</text>
  <text class="tagline-big" x="544" y="412">RESTORATION</text>
  <text class="tagline-big" x="544" y="462">EXPERIENCE</text>
  <text class="web" x="550" y="620">www.q-j-restoration.example</text>
</svg>

<!-- Inner spread -->
<svg class="sheet sheet--inner" viewBox="0 0 1000 707" xmlns="http://www.w3.org/2000/svg">
  <rect class="photo" x="0" y="0" width="1000" height="707" role="img" aria-label="Photo of a smiling older couple dancing in a bright modern living room"/>
  <polyline class="chevron-edge" points="603,-4 426,343 588,711"/>
  <polygon class="panel" points="618,0 1000,0 1000,707 603,707 440,343"/>

  <text class="headline" x="600" y="90">WATER OR</text>
  <text class="headline headline--blue" x="600" y="124">MOLD DAMAGE?</text>
  <text class="subhead" x="600" y="160">What happens after the cleanup?</text>

  <polygon class="pillar-band" points="525,183 1000,183 1000,221 506,221"/>
  <g>
    <circle class="tick-disc" cx="542" cy="202" r="7"/>
    <path class="tick" d="M538.5,202 l2.5,2.5 l4.5,-5"/>
    <text class="pillar" x="553" y="209">BUILD</text>
    <circle class="tick-disc" cx="650" cy="202" r="7"/>
    <path class="tick" d="M646.5,202 l2.5,2.5 l4.5,-5"/>
    <text class="pillar" x="661" y="209">RENOVATE</text>
    <circle class="tick-disc" cx="806" cy="202" r="7"/>
    <path class="tick" d="M802.5,202 l2.5,2.5 l4.5,-5"/>
    <text class="pillar" x="817" y="209">RESTORE</text>
  </g>

  <!-- Feature: Adjuster's Inspection -->
  <circle class="feature-ring" cx="545" cy="279" r="19"/>
  <circle class="feature-icon" cx="543" cy="277" r="6"/>
  <path class="feature-icon" d="M547.5,281.5 l6,6"/>
  <text class="feature-title" x="582" y="270">ADJUSTER'S</text>
  <text class="feature-title" x="582" y="290">INSPECTION</text>
  <text class="feature-body" x="582" y="316">Feel Confident. Be sure you</text>
  <text class="feature-body" x="582" y="328">received a fair and accurate</text>
  <text class="feature-body" x="582" y="340">assessment &amp; repair of all</text>
  <text class="feature-body" x="582" y="352">damages with our team's use</text>
  <text class="feature-body" x="582" y="364">of industry leading Estimating.</text>

  <!-- Feature: Timely Settlement -->
  <circle class="feature-ring" cx="769" cy="279" r="19"/>
  <circle class="feature-icon" cx="769" cy="279" r="8"/>
  <path class="feature-icon" d="M769,274 v5 l4,3"/>
  <text class="feature-title" x="802" y="270">TIMELY</text>
  <text class="feature-title" x="802" y="290">SETTLEMENT</text>
  <text class="feature-body" x="802" y="316">Don't wait. Minimize the hassle</text>
  <text class="feature-body" x="802" y="328">of long processing times from</text>
  <text class="feature-body" x="802" y="340">Estimate to Settlement when you</text>
  <text class="feature-body" x="802" y="352">team up with an Insurance</text>
  <text class="feature-body" x="802" y="364">Repair Specialist.</text>

  <!-- Feature: Under One Roof -->
  <circle class="feature-ring" cx="545" cy="425" r="19"/>
  <path class="feature-icon-fill" d="M535,426 l10,-10 l10,10 h-3 v9 h-14 v-9 z"/>
  <text class="feature-title" x="582" y="416">UNDER ONE</text>
  <text class="feature-title" x="582" y="436">ROOF</text>
  <text class="feature-body" x="582" y="462">Don't Worry. You won't need to</text>
  <text class="feature-body" x="582" y="474">arrange meetings with multiple</text>
  <text class="feature-body" x="582" y="486">contractors; we'll take care of</text>
  <text class="feature-body" x="582" y="498">everything from demo to final</text>
  <text class="feature-body" x="582" y="510">cleanup.</text>

  <!-- Feature: Superior Craftsmanship -->
  <circle class="feature-ring" cx="769" cy="425" r="19"/>
  <rect class="feature-icon" x="761" y="417" width="16" height="16" rx="2"/>
  <path class="feature-icon" d="M764.5,425 l3,3 l6,-7"/>
  <text class="feature-title" x="802" y="416">SUPERIOR</text>
  <text class="feature-title" x="802" y="436">CRAFTSMANSHIP</text>
  <text class="feature-body" x="802" y="462">Don't settle for satisfactory. Our</text>
  <text class="feature-body" x="802" y="474">team is committed to the highest</text>
  <text class="feature-body" x="802" y="486">standards of excellence every step</text>
  <text class="feature-body" x="802" y="498">of the way. Trust us when we say</text>
  <text class="feature-body" x="802" y="510">that we'll make you smile.</text>

  <text class="promise" x="778" y="565" text-anchor="middle">HERE FOR YOU, EVERY STEP OF THE WAY.</text>

  <text class="brand-name brand-name--light" x="778" y="625" font-size="24" text-anchor="middle">Q&amp;J Restoration</text>
</svg>

</body>
</html>
```